Construction company that specializes in roofing and siding

https://maplecrestbuild.example/featured-projects/

https://www.bramwickhomesllc.example/#

https://www.tallgrovecontractors.example/residential-siding-services/

Please model a website after these examples
I posted a doc that has some content to get you started. I will upload more content and photos as the site progresses.

Coded - Design and coding required

5+ page

```html
<!DOCTYPE html>
<html lang="en">
<head>
<meta charset="utf-8">
<title>Stoneward Construction — Roofing &amp; Siding in Minnesota</title>
<link href="https://fonts.googleapis.com/css2?family=Raleway:wght@300;400;600;700;800&family=Roboto:wght@300;400;500;700&display=swap" rel="stylesheet">
<style>
:root{
  --ink:#0c0c0c;
  --panel:#151515;
  --bar:#2a2a2a;
  --white:#ffffff;
  --soft:#d9d9d9;
  --muted:#9a9a9a;
  --grey-head:#8c8c8c;
  --line:#6a6a6a;
  --about:#4b4b4b;
}
*{box-sizing:border-box;margin:0;padding:0}
html,body{width:1200px;height:4212px;overflow:hidden}
body{background:var(--ink);color:var(--white);font-family:"Roboto",sans-serif;position:relative}
.abs{position:absolute}
a{color:inherit;text-decoration:none}

/* header */
.topbar{left:0;top:0;width:1200px;height:103px;background:#141414}
.navbar{left:0;top:103px;width:1200px;height:51px;background:var(--bar)}
.call-panel{left:0;top:0;width:1200px;height:154px}
.brand{display:flex;align-items:center;gap:14px;font-family:"Roboto",sans-serif;font-weight:700;font-size:26px;letter-spacing:1px;color:var(--white)}
.brand .mark{width:44px;height:44px;border:3px solid var(--white);border-radius:50%}
.social-top{top:42px;width:18px;height:18px;border:2px solid #8a8a8a;border-radius:3px}
.social-top.active{border-color:var(--white)}
.btn-outline{border:2px solid #cfcfcf;color:var(--white);font-size:14px;font-weight:500;display:flex;align-items:center;justify-content:center;letter-spacing:.3px}
.call-label{left:1117px;top:50px;font-size:13px;font-weight:700}
.call-phone{left:975px;top:86px;font-size:23px;font-weight:700;letter-spacing:.3px}
.nav{top:120px;font-size:12.5px;font-weight:500;color:var(--soft);letter-spacing:.2px}
.nav.current{color:var(--white);text-decoration:underline;text-underline-offset:4px}

/* hero */
.hero-photo{left:0;top:154px;width:1200px;height:626px;background:linear-gradient(100deg,#2f2f2f 0%,#555 40%,#6e6a5c 65%,#8a7a3a 78%,#4d4d45 100%)}
.hero-shade{left:0;top:154px;width:1200px;height:626px;background:linear-gradient(90deg,rgba(0,0,0,.55),rgba(0,0,0,.1) 60%,rgba(0,0,0,0))}
.hero-title{left:111px;top:333px;font-family:"Raleway",sans-serif;font-size:44px;line-height:54px}
.hero-title b{font-weight:800;display:block}
.hero-title span{font-weight:400;display:block}
.hero-text{left:111px;top:454px;width:460px;font-size:20px;line-height:31px;font-weight:300}
.btn-white{left:111px;top:543px;width:147px;height:44px;background:var(--white);color:#111;font-size:14px;font-weight:500;display:flex;align-items:center;justify-content:center}
.dot{top:735px;width:12px;height:12px;border:1.5px solid var(--white);border-radius:50%}
.dot.on{background:var(--white)}

/* section headings */
.section-title{width:1200px;left:0;text-align:center;font-family:"Raleway",sans-serif;font-size:48px}
.section-title b{color:var(--grey-head);font-weight:800}
.section-title span{color:var(--white);font-weight:400}
.tab{top:1020px;font-size:16px;color:var(--muted);font-weight:500}
.tab.current{color:var(--white);text-decoration:underline;text-underline-offset:4px}
.tab-sep{top:1020px;font-size:16px;color:var(--muted)}

/* service rows */
.photo{overflow:hidden}
.service-title{font-family:"Raleway",sans-serif;font-size:35px;line-height:46px}
.service-title b{display:block;color:var(--grey-head);font-weight:700}
.service-title b strong{color:var(--white);font-weight:700}
.service-text{width:420px;font-size:14.5px;line-height:26.5px;text-align:justify;color:var(--white)}
.btn-grad{background:linear-gradient(90deg,#3a3a3a,#6a6a6a);color:var(--white);font-size:14px;font-weight:500;display:flex;align-items:center;justify-content:center}

/* about */
.about{left:0;top:2523px;width:1200px;height:599px;background:linear-gradient(90deg,#444 0%,#505050 60%,#5a5a5a 100%)}
.about-title{left:111px;top:2656px;font-family:"Raleway",sans-serif;font-size:48px}
.about-title b{font-weight:800;color:#cfcfcf}
.about-title span{font-weight:400}
.about-sub{left:111px;top:2724px;font-size:21px;font-weight:700}
.about-text{left:111px;width:489px;font-size:14.5px;line-height:25.5px;text-align:justify}

/* promise */
.promise-box{left:136px;top:3237px;width:928px;height:438px;border:2px solid #555}
.promise-text{left:160px;width:880px;text-align:center;font-size:18.5px;line-height:31px;color:var(--white)}

/* footer */
.footer{left:0;top:3815px;width:1200px;height:397px;background:#151515}
.foot-head{top:3878px;font-size:16px;font-weight:700}
.foot-rule{top:3912px;height:2px;background:#cfcfcf}
.foot-text{font-size:13.5px;line-height:24px;color:#e6e6e6}
.foot-icon{width:30px;height:30px;border-radius:50%;background:#2b2b2b;display:flex;align-items:center;justify-content:center}
.copyright{left:0;top:4158px;width:1200px;text-align:center;font-size:13px;color:#e0e0e0}
</style>
</head>
<body>

<!-- header -->
<div class="abs topbar"></div>
<div class="abs navbar"></div>
<svg class="abs call-panel" viewBox="0 0 1200 154" aria-hidden="true">
  <polygon points="1000,0 1200,0 1200,154 913,154" fill="#262626"/>
</svg>
<div class="abs brand" style="left:111px;top:28px"><span class="mark"></span>STONEWARD</div>

<span class="abs social-top active" style="left:616px" aria-label="Our Page"></span>
<span class="abs social-top" style="left:660px" aria-label="Our Gallery"></span>
<span class="abs social-top" style="left:704px" aria-label="Our Network"></span>
<a class="abs btn-outline" style="left:762px;top:28px;width:137px;height:47px">CONTACT US</a>

<svg class="abs" style="left:1066px;top:40px" width="38" height="38" viewBox="0 0 38 38" aria-hidden="true">
  <path d="M12 8 l5 0 l2 7 l-3 3 a16 16 0 0 0 7 7 l3 -3 l7 2 l0 5 a3 3 0 0 1 -3 3 a24 24 0 0 1 -21 -21 a3 3 0 0 1 3 -3z" fill="#fff"/>
</svg>
<div class="abs call-label">CALL US:</div>
<div class="abs call-phone">+1 (555) 014 2200</div>

<a class="abs nav current" style="left:111px">HOME</a>
<a class="abs nav" style="left:177px">ABOUT US</a>
<a class="abs nav" style="left:268px">ROOFING &#8964;</a>
<a class="abs nav" style="left:366px">SIDING &#8964;</a>
<a class="abs nav" style="left:451px">GUTTERS</a>
<a class="abs nav" style="left:538px">WINDOWS</a>
<a class="abs nav" style="left:629px">REPAIR &#8964;</a>
<a class="abs nav" style="left:714px">STORM DAMAGE REPAIR &#8964;</a>

<!-- hero -->
<div class="abs hero-photo" role="img" aria-label="Roofer fastening asphalt shingles with a nail gun"></div>
<div class="abs hero-shade"></div>
<h1 class="abs hero-title"><b>STONEWARD</b><span>CONSTRUCTION</span></h1>
<p class="abs hero-text">Stoneward Construction is your source for roofing and siding in Minnesota.</p>
<a class="abs btn-white">GET STARTED</a>
<span class="abs dot" style="left:110px"></span>
<span class="abs dot on" style="left:140px"></span>
<span class="abs dot" style="left:167px"></span>
<span class="abs dot" style="left:197px"></span>

<!-- what we do -->
<h2 class="abs section-title" style="top:931px"><b>WHAT</b> <span>WE DO</span></h2>
<a class="abs tab current" style="left:152px">ROOFING</a>
<span class="abs tab-sep" style="left:258px">|</span>
<a class="abs tab" style="left:296px">SIDING</a>
<span class="abs tab-sep" style="left:385px">|</span>
<a class="abs tab" style="left:423px">GUTTERS</a>
<span class="abs tab-sep" style="left:533px">|</span>
<a class="abs tab" style="left:571px">WINDOWS</a>
<span class="abs tab-sep" style="left:685px">|</span>
<a class="abs tab" style="left:724px">REPAIR</a>
<span class="abs tab-sep" style="left:814px">|</span>
<a class="abs tab" style="left:853px">STORM DAMAGE REPAIR</a>

<!-- row 1 -->
<div class="abs photo" style="left:111px;top:1112px;width:489px;height:384px;background:linear-gradient(135deg,#6f7d3a 0%,#4a5a2a 30%,#9a9a9a 60%,#5e5e5e 100%)" role="img" aria-label="Worker nailing architectural shingles on a roof"></div>
<svg class="abs" style="left:550px;top:1253px" width="100" height="100" viewBox="0 0 100 100" aria-hidden="true">
  <polygon points="50,4 90,27 90,73 50,96 10,73 10,27" fill="#111" stroke="#3a3a3a" stroke-width="5"/>
  <path d="M32 64 L50 38 L68 64 Z" fill="none" stroke="#ddd" stroke-width="3"/>
  <path d="M40 64 V54 M50 64 V48 M60 64 V54" stroke="#ddd" stroke-width="3"/>
</svg>
<h3 class="abs service-title" style="left:669px;top:1153px"><b>ARCHITECTURAL</b><b>SHINGLES</b></h3>
<p class="abs service-text" style="left:669px;top:1261px">Architectural shingles are the most cost effective choice in roofing, that is why they are also the most common choice. At Stoneward Construction we specialize in replacing architectural shingle roofing.</p>
<a class="abs btn-outline" style="left:669px;top:1396px;width:147px;height:48px">LEARN MORE</a>

<!-- row 2 -->
<div class="abs photo" style="left:600px;top:1561px;width:489px;height:385px;background:linear-gradient(160deg,#c9cdd2 0%,#8b5a44 35%,#3a3a3a 60%,#5d7a3c 100%)" role="img" aria-label="Crew in safety vests installing steel roof framing"></div>
<svg class="abs" style="left:550px;top:1703px" width="100" height="100" viewBox="0 0 100 100" aria-hidden="true">
  <polygon points="50,4 90,27 90,73 50,96 10,73 10,27" fill="#111" stroke="#3a3a3a" stroke-width="5"/>
  <path d="M30 64 V40 H70 V64 M38 64 V40 M46 64 V40 M54 64 V40 M62 64 V40" fill="none" stroke="#ddd" stroke-width="3"/>
</svg>
<h3 class="abs service-title" style="left:111px;top:1603px"><b>STANDING <strong>SEAM</strong></b><b>STEEL <strong>ROOFING</strong></b></h3>
<p class="abs service-text" style="left:111px;top:1712px">Standing seam steel roofing is durable and long lasting. For homes and businesses, it is considered a premium upgrade over architectural shingles. While an architectural shingle roof in MN should typically be replaced after 20 years</p>
<a class="abs btn-grad" style="left:111px;top:1847px;width:147px;height:46px">LEARN MORE</a>

<!-- row 3 -->
<div class="abs photo" style="left:111px;top:2011px;width:489px;height:384px;background:linear-gradient(180deg,#e8e8e8 0%,#c47a3a 25%,#3c4a63 60%,#1d2638 100%)" role="img" aria-label="Workers fastening agricultural steel roofing panels"></div>
<svg class="abs" style="left:550px;top:2151px" width="100" height="100" viewBox="0 0 100 100" aria-hidden="true">
  <polygon points="50,4 90,27 90,73 50,96 10,73 10,27" fill="#111" stroke="#3a3a3a" stroke-width="5"/>
  <path d="M28 56 L52 38 L72 50 L48 68 Z" fill="none" stroke="#ddd" stroke-width="3"/>
</svg>
<h3 class="abs service-title" style="left:669px;top:2053px"><b>AGRICULTURAL</b><b>STEEL <strong>ROOFING</strong></b></h3>
<p class="abs service-text" style="left:669px;top:2162px">In MN there are a lot of shops, barns, and garages that require a cost effective and long lasting roofing system. Look no further than agricultural steel roofing panels. These panels are 3 feet wide and are ordered to the perfect length for your job.</p>
<a class="abs btn-outline" style="left:669px;top:2296px;width:147px;height:46px">LEARN MORE</a>

<!-- about -->
<div class="abs about" role="img" aria-label="Faded view of a home exterior with siding and stone"></div>
<h2 class="abs about-title"><b>ABOUT</b> <span>US</span></h2>
<p class="abs about-sub">FROM HUMBLE BEGINNINGS:</p>
<p class="abs about-text" style="top:2763px">In 2016 Dale Hartley started helping people with their home improvement projects. His very first job was installing window trim for a wonderful homeowner in Forest lake MN. He did his best work and made sure he treated his first customer like family. Afterall, his first customer was Marla Hartley, his Mom.</p>
<p class="abs about-text" style="top:2907px">Today, Dale and the Stoneward Construction team are helping homeowners around Minnesota; carrying the spirit of his first job onto every job they touch.</p>
<a class="abs btn-outline" style="left:111px;top:3013px;width:148px;height:48px">LEARN MORE</a>
<div class="abs" style="left:664px;top:2600px;width:422px;height:444px;background:linear-gradient(160deg,#5a5a5a,#777 50%,#8a8070 100%)" role="img" aria-label="House exterior with stone facade and windows"></div>

<!-- promise -->
<div class="abs promise-box"></div>
<h2 class="abs section-title" style="top:3350px"><b>THE STONEWARD</b> <span>PROMISE</span></h2>
<p class="abs promise-text" style="top:3438px">You deserve timely service, high quality materials, expert installation, and a rock-solid warranty. That is what we promise to deliver. I invite you to put us to the test today.</p>
<p class="abs promise-text" style="top:3518px">Sincerely,</p>
<p class="abs promise-text" style="top:3555px;font-size:26px;font-weight:700">Dale Hartley, Owner</p>
<p class="abs promise-text" style="top:3592px;font-size:12px;line-height:18px;font-weight:500">Stoneward Construction</p>
<a class="abs btn-grad" style="left:495px;top:3646px;width:210px;height:56px;font-size:18px">+1 (555) 014 2200</a>

<!-- footer -->
<div class="abs footer"></div>
<div class="abs brand" style="left:111px;top:3980px"><span class="mark"></span>STONEWARD</div>

<div class="abs foot-head" style="left:432px">CONTACT US</div>
<div class="abs foot-rule" style="left:432px;width:215px"></div>
<div class="abs foot-head" style="left:760px">QUICK LINKS</div>
<div class="abs foot-rule" style="left:760px;width:113px"></div>
<div class="abs foot-head" style="left:950px">FOLLOW US</div>
<div class="abs foot-rule" style="left:950px;width:114px"></div>

<span class="abs foot-icon" style="left:436px;top:3948px"><svg width="14" height="14" viewBox="0 0 14 14"><path d="M7 1a4 4 0 0 1 4 4c0 3-4 8-4 8s-4-5-4-8a4 4 0 0 1 4-4z" fill="#ddd"/><circle cx="7" cy="5" r="1.5" fill="#2b2b2b"/></svg></span>
<p class="abs foot-text" style="left:486px;top:3940px">465, Lorum Ipsum Dolore Sed,<br>United States</p>
<span class="abs foot-icon" style="left:436px;top:4010px"><svg width="14" height="14" viewBox="0 0 14 14"><path d="M3 1h3l1 3-2 2a7 7 0 0 0 3 3l2-2 3 1v3a1 1 0 0 1-1 1A11 11 0 0 1 2 2a1 1 0 0 1 1-1z" fill="#ddd"/></svg></span>
<p class="abs foot-text" style="left:486px;top:4000px">Call Us:<br>+1 (555) 014 2200</p>
<span class="abs foot-icon" style="left:436px;top:4072px"><svg width="14" height="14" viewBox="0 0 14 14"><rect x="1" y="3" width="12" height="8" fill="#ddd"/><path d="M1 3l6 5 6-5" fill="none" stroke="#2b2b2b" stroke-width="1.3"/></svg></span>
<p class="abs foot-text" style="left:486px;top:4060px">Email Us:<br>info@stonewardbuild.example</p>

<a class="abs foot-text" style="left:760px;top:3941px">Home</a>
<a class="abs foot-text" style="left:760px;top:3981px">About Us</a>
<a class="abs foot-text" style="left:760px;top:4021px">What We Do</a>
<a class="abs foot-text" style="left:760px;top:4061px">Contact Us</a>

<span class="abs foot-icon" style="left:955px;top:3950px"><span style="width:10px;height:10px;border:1.5px solid #ddd;border-radius:50%"></span></span>
<p class="abs foot-text" style="left:1005px;top:3941px">Follow Us On<br>OUR PAGE</p>
<span class="abs foot-icon" style="left:955px;top:4010px"><span style="width:10px;height:10px;border:1.5px solid #ddd;border-radius:50%"></span></span>
<p class="abs foot-text" style="left:1005px;top:4001px">Follow Us On<br>OUR GALLERY</p>
<span class="abs foot-icon" style="left:955px;top:4070px"><span style="width:10px;height:10px;border:1.5px solid #ddd;border-radius:50%"></span></span>
<p class="abs foot-text" style="left:1005px;top:4061px">Follow Us On<br>OUR NETWORK</p>

<div class="abs" style="left:0;top:4140px;width:1200px;height:1px;background:#2e2e2e"></div>
<p class="abs copyright">Copyright © 2024 STONEWARD CONSTRUCTION - All Rights Reserved.</p>

</body>
</html>
```